Optometrist A5 flyer update 2014

We are an optical / optometrist business needing an existing A5 flyer updated. This flyer has been very successful but needs to be renewed.
We are supplying all the original source files including images.
I have included pdf files with annotations on the alteration we would like made.
We are open to suggestions / alterations to the design of the pamphlet.
We are after a modern design appealing to the various ages of our patient base.

```html
<!DOCTYPE html>
<html lang="en">
<head>
<meta charset="utf-8">
<title>Belford Lane Optical – FAQ &amp; Opening Hours</title>
<link href="https://fonts.googleapis.com/css2?family=Fira+Sans:ital,wght@0,300;0,400;0,600;0,700;1,700&display=swap" rel="stylesheet">
<style>
  :root{
    --green:#009a00;
    --navy:#1b2a8f;
    --white:#ffffff;
    --frame-shadow:rgba(0,0,0,0.22);
  }
  *{margin:0;padding:0;box-sizing:border-box;}
  html,body{width:847px;height:1200px;overflow:hidden;background:var(--white);}
  .flyer{position:relative;width:847px;height:1200px;overflow:hidden;background:var(--white);font-family:"Fira Sans",Arial,sans-serif;}

  .info-panel{position:absolute;left:0;top:0;width:437px;height:1200px;background:var(--green);color:var(--white);z-index:5;}
  .section-title{position:absolute;left:47px;font-weight:300;font-size:44px;line-height:48px;letter-spacing:0.3px;}
  .faq-title{top:68px;}
  .hours-title{top:899px;}

  .faq{position:absolute;left:48px;width:370px;}
  .faq-question{position:relative;padding-left:22px;font-weight:700;font-style:italic;font-size:23px;line-height:30px;}
  .faq-question::before{content:"";position:absolute;left:1px;top:8px;border-left:11px solid var(--white);border-top:8px solid transparent;border-bottom:8px solid transparent;}
  .faq-answer{margin-top:12px;padding-left:22px;font-size:17px;line-height:23px;font-weight:400;}
  .faq-1{top:214px;}
  .faq-2{top:399px;}
  .faq-3{top:644px;}

  .hours{position:absolute;left:70px;top:960px;border-collapse:collapse;font-weight:700;font-size:18px;}
  .hours td{height:28px;padding:0;vertical-align:middle;}
  .hours .day{width:138px;}

  .photo{position:absolute;background:linear-gradient(150deg,#c9c4cf,#8f8a98 60%,#d8c7b4);}
  .photo-hero{left:437px;top:0;width:410px;height:413px;background:linear-gradient(160deg,#e6e2e8 0%,#a8a2b2 45%,#d9b48f 80%,#f0d47a 100%);}
  .photo-frame{position:absolute;background:var(--white);border-radius:14px;box-shadow:0 3px 8px var(--frame-shadow);padding:14px;}
  .photo-frame .photo{position:static;width:100%;height:100%;border-radius:2px;}
  .frame-girl{left:420px;top:356px;width:386px;height:248px;padding-left:17px;}
  .frame-girl .photo{background:linear-gradient(135deg,#b9c2d3,#8591a6 55%,#6b5044);}
  .frame-senior{left:420px;top:713px;width:364px;height:272px;padding-left:17px;}
  .frame-senior .photo{background:linear-gradient(150deg,#dfe6ea,#b8bec3 50%,#e2c2aa);}
  .frame-sunglasses{left:552px;top:555px;width:310px;height:250px;}
  .frame-sunglasses .photo{background:linear-gradient(140deg,#6d5a4c,#a88a72 50%,#4a3a31);}

  .brand{position:absolute;left:520px;top:1008px;width:250px;text-align:center;color:var(--navy);font-weight:400;font-size:34px;line-height:38px;}
  .brand-name-second{font-size:50px;line-height:52px;display:block;}

  .web-band{position:absolute;left:0;top:1133px;width:847px;height:67px;}
  .web-address{position:absolute;right:36px;top:1152px;color:var(--white);font-weight:700;font-size:21px;letter-spacing:0.2px;}
</style>
</head>
<body>
<main class="flyer">
  <div class="photo photo-hero" role="img" aria-label="Photo of a father in glasses and his young son in glasses looking at a tablet"></div>
  <div class="photo-frame frame-girl"><div class="photo" role="img" aria-label="Photo of a smiling girl wearing black-rimmed glasses"></div></div>
  <div class="photo-frame frame-senior"><div class="photo" role="img" aria-label="Photo of a smiling older woman wearing glasses"></div></div>
  <div class="photo-frame frame-sunglasses"><div class="photo" role="img" aria-label="Photo of a smiling young woman wearing sunglasses"></div></div>

  <section class="info-panel">
    <h1 class="section-title faq-title">Frequently Asked<br>Questions</h1>

    <div class="faq faq-1">
      <h2 class="faq-question">Can I have fashion sunglasses made to my prescription?</h2>
      <p class="faq-answer">Yes. It does depend on the sunglasses and your prescription.<br>We offer a range of sunglasses that can be fitted with prescription lenses.</p>
    </div>

    <div class="faq faq-2">
      <h2 class="faq-question">If I want new prescription lenses fitted to my existing pair of glasses, do I have to go without them for a week?</h2>
      <p class="faq-answer">No. We can usually fit new lenses to your own frame onsite.<br>You only need to be without your glass-es for a few hours.</p>
    </div>

    <div class="faq faq-3">
      <h2 class="faq-question">Do I have to purchase my spectacles where my private health fund directs?</h2>
      <p class="faq-answer">No. It is your decision where to have your eyes tested and where to purchase your spectacles or contact lenses. We can direct bill your private health fund with the ClaimPoint system.</p>
    </div>

    <h2 class="section-title hours-title">Opening Hours</h2>
    <table class="hours">
      <tr><td class="day">Monday</td><td>9.00am - 5.30pm</td></tr>
      <tr><td class="day">Tuesday</td><td>9.00am - 6.30pm</td></tr>
      <tr><td class="day">Wednesday</td><td>9.00am - 5.30pm</td></tr>
      <tr><td class="day">Thursday</td><td>9.00am - 6.30pm</td></tr>
      <tr><td class="day">Friday</td><td>9.00am - 5.30pm</td></tr>
      <tr><td class="day">Saturday</td><td>9.00am - 1.00pm</td></tr>
    </table>
  </section>

  <div class="brand">Belford Lane<span class="brand-name-second">Optical</span></div>

  <svg class="web-band" viewBox="0 0 847 67" aria-hidden="true">
    <polygon points="403,0 847,0 847,67 368,67" fill="var(--navy)"/>
  </svg>
  <p class="web-address">www.belfordlaneoptical.com.au</p>
</main>
</body>
</html>
```